Small environmental consultancy needs a simple but professional web design

We are a boutique environmental consultancyand contracting business located in Margaret River in the South West of Western Australia.

We have two arms
1) Consulting which offers environmental planning, management and assessment services primarily to local government and the development industry.
2) Contracting which implements on site plans and on ground works primarily involving revegetation, bush regeneration and environmental weed control.

We need a simple yet professional web design within the wordpress platform that commmunicates professionalism, experience and technical expertise without appearing too corporate.

Something like this structure appeals:
http://fernquill.net.au/environment-services/
or
http://www.tallowbrookenvironmental.com.au/index.php

(without the image gallery function)

Target Market(s)

Local Government Officers deciding on tenders;
Developers, Engineers, Town Planning consultants looking for environmental expertise

Industry/Entity Type

Business

Number of Pages Required

5+ page

Font styles to use
Sans Serif

Colors
33a6d7
9bcb3c

Requirements
Must have
• Pages required include:
• Home
• Environmental Planning and Management
• Revegetation and Regeneration Implementation (This page can mirror the Environmental Planning and Management page exactly in structure but with different text and images)
• About Us (I think that this page can be relatively simple and generic)
• Contact (I think that this page can be very simple and generic)
Nice to have
• An ability to start out basic and quicikly establish a website presence and then build in additional drop downs and pages over time.
Should not have
• It does not need a photo gallery page;
• It does not need a major amount of space dedicated to social media and blogs etc as this is not currently particularly active area for us

```html
<!DOCTYPE html>
<html lang="en">
<head>
<meta charset="utf-8">
<title>Wandoo Ecoservices</title>
<link rel="stylesheet" href="https://fonts.googleapis.com/css2?family=Exo+2:wght@400;500;600;700&family=Open+Sans:wght@400;600;700&display=swap">
<style>
:root{
  --green:#9bcb3c;
  --green-dark:#7aa620;
  --green-deep:#4f7a12;
  --blue:#33a6d7;
  --ink:#222;
  --text:#555;
  --muted:#777;
  --sand:#ecebe3;
  --foot:#e8e8e8;
  --white:#fff;
}
*{box-sizing:border-box;margin:0;padding:0}
html,body{width:689px;height:1200px;overflow:hidden;background:var(--white)}
body{position:relative;font-family:"Open Sans",Arial,sans-serif;color:var(--text)}
.abs{position:absolute}
.head{font-family:"Exo 2",Arial,sans-serif}

/* header */
.site-header{left:0;top:0;width:689px;height:68px;background:linear-gradient(180deg,#a6d244 0%,var(--green-dark) 100%)}
.brand{left:0;top:0;width:180px;height:68px;background:var(--white);clip-path:polygon(0 0,100% 0,85% 100%,0 100%)}
.brand-mark{left:84px;top:6px;width:26px;height:26px;border-radius:50%;background:var(--green)}
.brand-name{left:58px;top:44px;font-family:"Exo 2",sans-serif;font-size:12px;font-weight:600;color:var(--green-deep);white-space:nowrap}
.search{left:187px;top:3px;width:106px;height:14px;border-radius:7px;background:var(--white);font-size:6px;color:#999;padding:3px 8px}
.search-btn{left:280px;top:3px;width:14px;height:14px;border-radius:50%;background:var(--green-deep)}
.call-top{left:538px;top:4px;font-family:"Exo 2",sans-serif;font-size:7px;font-weight:700;color:var(--white)}
.nav{left:176px;top:40px;display:flex;align-items:center;gap:14px;font-family:"Exo 2",sans-serif;font-size:7.5px;font-weight:500;color:var(--white);text-transform:uppercase;white-space:nowrap}

/* hero */
.hero{left:0;top:68px;width:689px;height:364px;background:radial-gradient(ellipse at 50% 30%,#d9f07a 0%,#8fc23a 35%,#4f8a1c 70%,#2f5a12 100%)}
.hero-title{left:57px;top:172px;font-family:"Exo 2",sans-serif;font-size:25px;font-weight:700;color:#111;letter-spacing:.2px}
.hero-sub{left:57px;top:202px;font-family:"Exo 2",sans-serif;font-size:15px;font-weight:500;color:#111}
.feature{top:300px;width:162px;height:132px;background:rgba(255,255,255,.82)}
.feature-head{height:34px;background:var(--blue);color:var(--white);font-family:"Exo 2",sans-serif;font-size:11.5px;font-weight:500;line-height:12px;padding:5px 9px;text-transform:uppercase}
.feature p{font-size:7px;line-height:12px;color:#444;padding:7px 9px 0}
.feature a{position:absolute;left:9px;top:111px;font-size:6.5px;color:var(--blue);text-decoration:none}
.slider-dots{left:548px;top:404px;width:82px;height:22px;border-radius:11px;background:var(--green-deep);display:flex;align-items:center;gap:4px;padding-left:8px}
.slider-dots span{width:10px;height:10px;border-radius:50%;border:1.5px solid var(--white)}
.slider-dots span.on{background:var(--white)}

/* welcome */
.welcome-title{left:0;top:456px;width:689px;text-align:center;font-family:"Exo 2",sans-serif;font-size:18px;color:#333}
.welcome-title b{color:var(--green);font-weight:500}
.welcome-text{left:60px;top:487px;width:570px;text-align:center;font-size:7.2px;line-height:12.5px;color:var(--text)}

/* cards */
.cards-band{left:0;top:565px;width:689px;height:224px;background:var(--sand)}
.card{top:580px;width:133px;height:194px;background:var(--white);box-shadow:0 0 2px rgba(0,0,0,.12)}
.card-img{position:absolute;left:2px;top:2px;width:129px;height:94px}
.card h3{position:absolute;left:7px;top:104px;font-size:7px;font-weight:700;color:var(--ink);text-transform:uppercase}
.card p{position:absolute;left:7px;top:118px;width:122px;font-size:7px;line-height:13px;color:var(--text)}
.card a{position:absolute;left:7px;top:175px;font-size:6.5px;color:var(--blue);text-decoration:none}

/* testimonials */
.clients-title{left:0;top:803px;width:689px;text-align:center;font-family:"Exo 2",sans-serif;font-size:18px;color:#333}
.clients-title b{font-weight:500;color:#222}
.clients-rule{left:334px;top:835px;width:20px;height:2px;background:var(--blue)}
.quote{top:862px;width:150px}
.quote-mark{position:absolute;left:0;top:-2px;font-family:Georgia,serif;font-size:30px;line-height:30px;color:var(--green);font-weight:700}
.quote p{position:absolute;left:21px;top:6px;width:120px;font-size:7px;line-height:11.5px;color:var(--text)}
.quote h4{position:absolute;left:21px;top:56px;font-size:7px;font-weight:700;color:var(--ink)}
.avatar{position:absolute;left:14px;top:74px;width:67px;height:67px;border-radius:50%;border:2px solid #ddd;background:linear-gradient(180deg,#c9c4bd,#8f8a84)}
.arrow{top:922px}

/* footer */
.footer{left:0;top:1024px;width:689px;height:176px;background:var(--foot)}
.foot-h{font-family:"Exo 2",sans-serif;font-size:10px;font-weight:600;color:#333;text-transform:uppercase}
.foot-h span{font-weight:400}
.foot-links{font-size:6.5px;line-height:11px;color:#333;list-style:none}
.phone{left:57px;top:1127px;display:flex;align-items:center;gap:6px;font-family:"Exo 2",sans-serif;font-size:12px;color:var(--green-dark)}
.field{height:19px;background:var(--white);border:1px solid #d6d6d6;font-size:8px;color:#aaa;padding:3px 7px}
.send{left:352px;top:1133px;width:83px;height:23px;background:linear-gradient(180deg,#9bcb3c,#6f9a1c);color:var(--white);font-family:"Exo 2",sans-serif;font-size:9px;font-weight:500;text-align:center;line-height:23px}
.foot-rule{left:57px;top:1172px;width:575px;height:1px;background:#d8d8d8}
.copyright{left:57px;top:1181px;font-size:6.5px;color:#333}
</style>
</head>
<body>

<header class="site-header abs"></header>
<div class="brand abs"></div>
<div class="brand-mark abs"></div>
<div class="brand-name abs">Wandoo Ecoservices</div>
<div class="search abs">Search</div>
<div class="search-btn abs"></div>
<div class="call-top abs">CALL US NOW: 0897 000 000</div>
<nav class="nav abs">
  <svg width="12" height="11" viewBox="0 0 12 11"><path d="M6 0L0 5h1.6v6h3.2V7.5h2.4V11h3.2V5H12z" fill="#fff"/></svg>
  <span>Environmental Planning and Management</span>
  <span>Revegetation and Bush Regeneration</span>
  <span>About Us</span>
  <span>Contacts</span>
</nav>

<section class="hero abs" role="img" aria-label="Forest canopy seen from below, tall tree trunks and bright green leaves"></section>
<h1 class="hero-title abs">LOREM IPSUM DOLOR SIT AMET</h1>
<div class="hero-sub abs">CONSECTETUR ADIPISCING ELIT</div>

<div class="feature abs" style="left:57px">
  <div class="feature-head">What<br>we do</div>
  <p>Nam nec tellus a odio tincidunt auctor a ornare odio. Sed non mauris vitae erat consequat auctor eu in elit. Class aptent taciti sociosqu ad litora torquent per conubia nostra.</p>
  <a href="#">READ MORE</a>
</div>
<div class="feature abs" style="left:219px">
  <div class="feature-head">Our<br>philoshophy</div>
  <p>Nam nec tellus a odio tincidunt auctor a ornare odio. Sed non mauris vitae erat consequat auctor eu in elit. Class aptent taciti sociosqu ad litora torquent per conubia nostra.</p>
  <a href="#">READ MORE</a>
</div>
<div class="feature abs" style="left:382px">
  <div class="feature-head">Our<br>vision</div>
  <p>Nam nec tellus a odio tincidunt auctor a ornare odio. Sed non mauris vitae erat consequat auctor eu in elit. Class aptent taciti sociosqu ad litora torquent per conubia nostra.</p>
  <a href="#">READ MORE</a>
</div>
<div class="slider-dots abs"><span class="on"></span><span></span><span></span><span></span><span></span></div>

<h2 class="welcome-title abs">WELCOME TO <b>WANDOO ECOSERVICES</b></h2>
<p class="welcome-text abs">Lorem ipsum dolor sit amet, consectetur adipiscing elit, sed do eiusmod tempor incididunt ut labore et dolore magna aliqua. Ut enim ad minim veniam, quis nostrud exercitation ullamco laboris nisi ut aliquip ex ea commodo consequat. Duis aute irure dolor in reprehenderit in voluptate velit esse cillum dolore eu fugiat nulla pariatur. Excepteur sint occaecat cupidatat non proident, sunt in culpa qui officia deserunt mollit anim id est laborum. Lorem ipsum dolor sit amet, consectetur adipiscing elit, sed do eiusmod tempor incididunt ut labore et dolore magna aliqua.</p>

<div class="cards-band abs"></div>
<article class="card abs" style="left:57px">
  <div class="card-img" role="img" aria-label="Business handshake in front of a green forest" style="background:linear-gradient(135deg,#5d7a3a,#2f4a22)"></div>
  <h3>About us</h3>
  <p>Lorem ipsum dolor sit amet, consectetur adipiscing elit, sed do eiusmod tempor incididunt ut labore et dolore.</p>
  <a href="#">READ MORE &#9656;</a>
</article>
<article class="card abs" style="left:205px">
  <div class="card-img" role="img" aria-label="Pink thistle flower close up" style="background:linear-gradient(180deg,#d23fa8,#7a9a3c)"></div>
  <h3>Our services</h3>
  <p>Lorem ipsum dolor sit amet, consectetur adipiscing elit, sed do eiusmod tempor incididunt ut labore et dolore.</p>
  <a href="#">READ MORE &#9656;</a>
</article>
<article class="card abs" style="left:353px">
  <div class="card-img" role="img" aria-label="Pink and white cosmos flowers on green" style="background:linear-gradient(135deg,#e99ac0,#6ea24a)"></div>
  <h3>Current project</h3>
  <p>Lorem ipsum dolor sit amet, consectetur adipiscing elit, sed do eiusmod tempor incididunt ut labore et dolore.</p>
  <a href="#">READ MORE &#9656;</a>
</article>
<article class="card abs" style="left:501px">
  <div class="card-img" role="img" aria-label="Purple bellflowers in a meadow" style="background:linear-gradient(135deg,#6a4fb5,#8aa83a)"></div>
  <h3>Why us?</h3>
  <p>Lorem ipsum dolor sit amet, consectetur adipiscing elit, sed do eiusmod tempor incididunt ut labore et dolore.</p>
  <a href="#">READ MORE &#9656;</a>
</article>

<h2 class="clients-title abs"><b>WHAT</b> OUR CLIENTS THINK</h2>
<div class="clients-rule abs"></div>
<svg class="arrow abs" style="left:64px" width="12" height="24" viewBox="0 0 12 24"><path d="M11 1L1 12l10 11" fill="none" stroke="#bbb" stroke-width="1.2"/></svg>
<svg class="arrow abs" style="left:612px" width="12" height="24" viewBox="0 0 12 24"><path d="M1 1l10 11L1 23" fill="none" stroke="#bbb" stroke-width="1.2"/></svg>

<div class="quote abs" style="left:97px">
  <span class="quote-mark">&ldquo;</span>
  <p>Lorem ipsum dolor sit amet, consectetur adipiscing elit, sed do eiusmod tempor incididunt ut labore et dolore magna aliqua.</p>
  <h4>Daniel Shore</h4>
  <div class="avatar" role="img" aria-label="Client portrait"></div>
</div>
<div class="quote abs" style="left:278px">
  <span class="quote-mark">&ldquo;</span>
  <p>Lorem ipsum dolor sit amet, consectetur adipiscing elit, sed do eiusmod tempor incididunt ut labore et dolore magna aliqua.</p>
  <h4>Tom Fenwick</h4>
  <div class="avatar" role="img" aria-label="Client portrait"></div>
</div>
<div class="quote abs" style="left:459px">
  <span class="quote-mark">&ldquo;</span>
  <p>Lorem ipsum dolor sit amet, consectetur adipiscing elit, sed do eiusmod tempor incididunt ut labore et dolore magna aliqua.</p>
  <h4>Daniel Shore</h4>
  <div class="avatar" role="img" aria-label="Client portrait"></div>
</div>

<footer class="footer abs"></footer>
<div class="foot-h abs" style="left:57px;top:1041px">About</div>
<ul class="foot-links abs" style="left:57px;top:1057px">
  <li>Environmental Planning and Management</li>
  <li>Revegetation and Bush Regeneration</li>
  <li>Contacts</li>
</ul>
<div class="foot-h abs" style="left:231px;top:1041px">Legal</div>
<ul class="foot-links abs" style="left:231px;top:1057px">
  <li>Terms of Service</li>
  <li>Privacy Policy</li>
  <li>Cookie Policy</li>
</ul>
<div class="foot-h abs" style="left:57px;top:1107px">Call <span>us now:</span></div>
<div class="phone abs">
  <svg width="11" height="11" viewBox="0 0 24 24"><path d="M6.6 10.8a15 15 0 006.6 6.6l2.2-2.2c.3-.3.7-.4 1-.2 1.1.4 2.3.6 3.6.6.6 0 1 .4 1 1V20c0 .6-.4 1-1 1C10.6 21 3 13.4 3 4c0-.6.4-1 1-1h3.5c.6 0 1 .4 1 1 0 1.3.2 2.5.6 3.6.1.3 0 .7-.2 1z" fill="#444"/></svg>
  +0897 000 000
</div>
<div class="foot-h abs" style="left:352px;top:1045px">Contact <span>us</span></div>
<div class="field abs" style="left:352px;top:1064px;width:132px">Name</div>
<svg class="abs" style="left:469px;top:1068px" width="10" height="10" viewBox="0 0 10 10"><circle cx="5" cy="3" r="2.4" fill="#aaa"/><path d="M0 10c0-3 2.2-4.5 5-4.5S10 7 10 10z" fill="#aaa"/></svg>
<div class="field abs" style="left:489px;top:1064px;width:133px">E-mail</div>
<svg class="abs" style="left:605px;top:1069px" width="11" height="8" viewBox="0 0 11 8"><rect width="11" height="8" fill="#aaa"/><path d="M0 0l5.5 4.5L11 0" fill="none" stroke="#fff" stroke-width="1"/></svg>
<div class="field abs" style="left:352px;top:1088px;width:270px;height:40px">Message</div>
<svg class="abs" style="left:606px;top:1091px" width="11" height="9" viewBox="0 0 11 9"><path d="M0 0h11v6H4L1.5 9V6H0z" fill="#aaa"/></svg>
<div class="send abs">Send Message</div>
<div class="foot-rule abs"></div>
<div class="copyright abs">&copy; 2015, Wandoo Ecoservices. All Rights Reserved.</div>

</body>
</html>
```